I'm looking for a smart new design for business cards

Industry/Entity Type

Commercial Electrical

Contact Information for Business Card

Logo, name, email, position, website QR

Requirements
Nice to have
• Logo embedded behind the text side

```html
<!DOCTYPE html>
<html lang="en">
<head>
<meta charset="utf-8">
<title>Voltline Trade Services – Business Card</title>
<link href="https://fonts.googleapis.com/css2?family=Montserrat:wght@400;500;700&display=swap" rel="stylesheet">
<style>
  :root{
    --bg:#d0d5d6;
    --card:#f2f2f1;
    --navy:#2a2a7a;
    --red:#e01e2b;
    --ink:#2b2b2b;
    --muted:#4a4a4a;
  }
  *{box-sizing:border-box;margin:0;padding:0}
  html,body{width:1200px;height:881px;overflow:hidden}
  body{background:var(--bg);font-family:"Montserrat",sans-serif;position:relative}
  .card{
    position:absolute;width:520px;height:297px;background:var(--card);
    border-bottom:4px solid var(--red);
    box-shadow:0 10px 24px rgba(0,0,0,.18);
  }
  .card--front{left:50px;top:292px}
  .card--back{left:630px;top:292px}

  .brand{display:flex;align-items:center;gap:10px;color:var(--navy);font-weight:700;text-transform:uppercase;line-height:1.15}
  .brand__dot{width:18px;height:18px;border-radius:50%;background:var(--red);flex:none}

  .card--front .brand{position:absolute;left:34px;top:110px;width:200px;font-size:19px}
  .divider{position:absolute;left:252px;top:58px;width:2px;height:184px;background:var(--red)}
  .contact{position:absolute;left:276px;top:62px;color:var(--ink)}
  .contact__name{font-size:24px;font-weight:700;color:var(--navy)}
  .contact__name span{color:var(--red)}
  .contact__role{font-size:13px;color:var(--muted);margin:4px 0 14px}
  .contact__address{font-size:12.5px;color:var(--muted);line-height:1.45;margin-bottom:10px}
  .contact__list{list-style:none;font-size:12.5px;color:var(--muted)}
  .contact__list li{display:flex;align-items:center;gap:8px;line-height:1.7}
  .contact__list svg{width:12px;height:12px;fill:var(--red);flex:none}

  .card--back .brand{position:absolute;left:0;right:0;top:0;bottom:0;justify-content:center;font-size:28px;gap:14px}
  .card--back .brand__dot{width:26px;height:26px}
</style>
</head>
<body>
  <section class="card card--front">
    <div class="brand"><span class="brand__dot"></span><span>Voltline Trade Services</span></div>
    <div class="divider"></div>
    <div class="contact">
      <h1 class="contact__name">Daniel <span>Marsh</span></h1>
      <p class="contact__role">Managing Director</p>
      <p class="contact__address">Your address, City<br>State, Zip 1234</p>
      <ul class="contact__list">
        <li><svg viewBox="0 0 24 24"><path d="M6.6 10.8a15 15 0 0 0 6.6 6.6l2.2-2.2a1 1 0 0 1 1-.25 11.4 11.4 0 0 0 3.6.57 1 1 0 0 1 1 1V20a1 1 0 0 1-1 1A17 17 0 0 1 3 4a1 1 0 0 1 1-1h3.5a1 1 0 0 1 1 1c0 1.25.2 2.45.57 3.57a1 1 0 0 1-.25 1z"/></svg>123 456 789</li>
        <li><svg viewBox="0 0 24 24"><path d="M2 5h20v14H2z M2 5l10 8 10-8" stroke="#f2f2f1" stroke-width="1.5"/></svg>hello@voltlinetrade.com</li>
        <li><svg viewBox="0 0 24 24"><circle cx="12" cy="12" r="10"/></svg>www.voltlinetrade.com</li>
      </ul>
    </div>
  </section>

  <section class="card card--back">
    <div class="brand"><span class="brand__dot"></span><span>Voltline Trade Services</span></div>
  </section>
</body>
</html>
```